Stationery Design Task - Stationary, memo and report templates for professional services company

Looking for someone to update stationary design but just as importantly come up with a template for reports and memos for use in our consulting firm. Would also like some brand use guidelines to be able to share with our whole team. We have an existing logo that we like. Need to update with a more contemporary look so that our deliverables to clients look good and professional yet stylish. This is for business to business communications. No need for envelope design. Important to have design for multiple pages, i.e. first page of a report and then 2nd page. Need to use in MS word documents so must be easy to use and replicate. Don't want something overly complex. Clean, fresh looking is best.

Industry/Entity Type

Information Technology

Font styles to use
Sans Serif

Colors
33a6d7
0792cd
85cae6
cee9f5
cedeed
85abd2
3377b5
0455a3

Requirements
Must have
• Clean look but with a little style or pop. Something that can easily be used in word documents. Need to have page styles that have a first page of a report (not a cover page) and then secondary page.
Nice to have
• - Although the dark blue is our primary color. Might be willing to look at some accent color as well.
Should not have
• Not just our logo on the page with a color bar.

```html
<!DOCTYPE html>
<html lang="en">
<head>
<meta charset="utf-8">
<title>Kestrel Tech Stationery</title>
<link rel="stylesheet" href="https://fonts.googleapis.com/css2?family=Roboto:wght@400;500;700&family=Questrial&display=swap">
<style>
  :root {
    --stage: #666666;
    --navy: #0455a3;
    --blue: #0b6fb6;
    --sky: #2a8fcf;
    --steel: #4f8fb8;
    --ink: #4a4a4a;
    --muted: #6a6a6a;
    --rule: #7a7a7a;
    --white: #ffffff;
  }
  * { margin: 0; padding: 0; box-sizing: border-box; }
  html, body { width: 1200px; height: 578px; overflow: hidden; background: var(--stage); }
  .canvas { position: relative; width: 1200px; height: 578px; }
  .page { position: absolute; top: 53px; width: 338px; height: 474px; overflow: hidden; }
  .page--cover { left: 62px; background: linear-gradient(180deg, #f4f4f4 0%, #dcdcdc 60%, #c8c8c8 100%); font-family: "Roboto", sans-serif; }
  .page--letter { left: 434px; background: linear-gradient(180deg, #f6f6f6 0%, #e2e2e2 55%, #cfcfcf 100%); font-family: "Questrial", sans-serif; }
  .page--follow { left: 806px; background: linear-gradient(90deg, #d6d6d6 0%, #e6e6e6 45%, #fafafa 80%, #ffffff 100%); }
  .cover-shapes { position: absolute; inset: 0; width: 100%; height: 100%; }

  .brand { position: absolute; display: flex; align-items: center; gap: 7px; color: var(--blue); font-family: "Roboto", sans-serif; font-weight: 700; white-space: nowrap; }
  .brand__dot { border-radius: 50%; background: var(--blue); }
  .brand--cover { left: 0; right: 0; top: 38px; justify-content: center; font-size: 24px; letter-spacing: 0.5px; }
  .brand--cover .brand__dot { width: 26px; height: 26px; }
  .brand--letter { left: 190px; top: 38px; font-size: 17px; }
  .brand--letter .brand__dot { width: 20px; height: 20px; }

  .report-title { position: absolute; left: 0; width: 332px; top: 190px; text-align: center; color: var(--white); }
  .report-title__main { font-weight: 700; font-size: 31px; line-height: 36px; letter-spacing: 0.3px; }
  .report-title__sub { font-weight: 500; font-size: 12.5px; margin-top: 4px; }

  .prepared { position: absolute; left: 27px; top: 445px; }
  .prepared { top: 394px; }
  .prepared__label { color: var(--blue); font-weight: 700; font-size: 11.5px; letter-spacing: 0.2px; }
  .prepared__name { color: var(--muted); font-size: 10.5px; margin-top: 1px; }
  .prepared__rule { width: 171px; height: 1px; background: var(--rule); margin-top: 8px; }
  .dates { display: flex; gap: 24px; margin-top: 8px; font-size: 8.5px; }
  .dates__label { color: var(--blue); }
  .dates__value { color: var(--ink); margin-top: 1px; }

  .sender { position: absolute; left: 30px; top: 34px; font-size: 5.8px; color: var(--ink); letter-spacing: 0.1px; }
  .sender__line { padding: 2px 0 2px; border-bottom: 0.6px solid var(--rule); width: 143px; }
  .sender__line:last-child { border-bottom: none; }
  .letter-body { position: absolute; left: 30px; top: 134px; width: 283px; color: var(--ink); }
  .letter-body__greeting { font-size: 8.5px; margin-bottom: 12px; }
  .letter-body p { font-size: 4.5px; line-height: 7.3px; margin-bottom: 6px; color: #555; text-align: justify; }
  .letter-body__closing { font-size: 4.5px; margin-top: 12px; color: #555; }
  .signature { width: 66px; height: 26px; margin-top: 6px; background: linear-gradient(90deg, rgba(11,111,182,0.18), rgba(11,111,182,0.05)); border-radius: 3px; }
</style>
</head>
<body>
<main class="canvas">

  <section class="page page--cover">
    <svg class="cover-shapes" viewBox="0 0 422 593" preserveAspectRatio="none" aria-hidden="true">
      <defs>
        <linearGradient id="sideBlue" x1="0" y1="0" x2="0" y2="1">
          <stop offset="0" stop-color="#2a94d3"/>
          <stop offset="1" stop-color="#1f7fc0"/>
        </linearGradient>
        <linearGradient id="heroBlue" x1="0" y1="0" x2="0" y2="1">
          <stop offset="0" stop-color="#0c6db4"/>
          <stop offset="1" stop-color="#0a64aa"/>
        </linearGradient>
        <linearGradient id="steelBlue" x1="0" y1="0" x2="0" y2="1">
          <stop offset="0" stop-color="#5a9cc6"/>
          <stop offset="1" stop-color="#4b88b0"/>
        </linearGradient>
      </defs>
      <polygon points="8,7 47,7 111,139 8,289" fill="url(#sideBlue)"/>
      <polygon points="83,140 333,140 396,296 333,452 83,452 23,296" fill="url(#heroBlue)"/>
      <polygon points="411,299 411,582 367,582 313,454" fill="url(#steelBlue)"/>
    </svg>

    <div class="brand brand--cover"><span class="brand__dot"></span>KESTREL TECH</div>

    <div class="report-title">
      <h1 class="report-title__main">REPORT<br>TITLE HERE</h1>
      <p class="report-title__sub">YOUR SUBTITLE HERE</p>
    </div>

    <div class="prepared">
      <p class="prepared__label">REPORT PREPARED BY</p>
      <p class="prepared__name">YOUR NAME HERE</p>
      <div class="prepared__rule"></div>
      <div class="dates">
        <div><p class="dates__label">PROPOSAL ISSUED</p><p class="dates__value">SEP 19,2018</p></div>
        <div><p class="dates__label">PROPOSAL VALID TO</p><p class="dates__value">SEP 19,2019</p></div>
      </div>
    </div>
  </section>

  <section class="page page--letter">
    <div class="sender">
      <p class="sender__line">1420 CEDAR ROW, FAIRBANKS, ALASKA 99701</p>
      <p class="sender__line">555 210 4478 | INFO@KESTRELTECH.COM</p>
      <p class="sender__line">WWW.KESTRELTECH.COM</p>
    </div>

    <div class="brand brand--letter"><span class="brand__dot"></span>KESTREL TECH</div>

    <div class="letter-body">
      <p class="letter-body__greeting">Dear Ms. Carter,</p>
      <p>Lorem ipsum dolor sit amet, consectetur adipiscing elit. Donec orci purus, luctus vitae dignissim eu, iaculis sed purus. Vivamus faucibus, ipsum nec aliquet viverra, leo mauris condimentum ligula, sit amet sagittis enim ligula quis arcu. Nam egestas tortor id nisi porttitor mattis. In tortor ante, ultricies in suscipit a, tempus non massa. Vivamus et auctor mi. Fusce vel massa nulla. Phasellus nec eros mauris, et scelerisque orci.</p>
      <p>Donec malesuada orci vitae nulla accumsan porta a id massa. Quisque accumsan iaculis magna sit amet fringilla. Maecenas consequat, magna eget tincidunt semper, odio nibh rutrum mi, id feugiat ante nisl eu risus. Vestibulum nunc orci, rhoncus a placerat in, ultricies in mi. Cras mattis varius eros, vel fringilla nisl suscipit eget. Quisque scelerisque sagittis nulla at porttitor.</p>
      <p>Sed id augue vitae urna euismod commodo aliquet a quam. Pellentesque arcu velit, cursus et malesuada ut, consequat et diam. Nullam erat sem, rhoncus id ullamcorper vitae, rhoncus et arcu. In ultricies ultricies nulla, ut rutrum nisl iaculis at. Donec eu magna a metus ornare faucibus. Fusce aliquet faucibus ultricies. Morbi semper, est id tincidunt gravida, sem arcu adipiscing lacus, ac bibendum nulla leo eu purus. Quisque nec diam sed risus consectetur a accumsan quis nibh. Vestibulum id purus lorem.</p>
      <p>It is a long established fact that a reader will be distracted by the readable content of a page when looking at its layout. The point of using Lorem Ipsum is that it has a more-or-less normal distribution of letters, as opposed to using 'Content here, content here', making it look like readable English. Many desktop publishing packages</p>
      <p class="letter-body__closing">Sincerely,</p>
      <div class="signature" role="img" aria-label="Handwritten signature of Ellen Carter"></div>
    </div>
  </section>

  <section class="page page--follow" aria-label="Continuation page"></section>

</main>
</body>
</html>
```